Wholesale in Gold Jewellery & Gold Bullion

We are an established gold jewellery and gold bullion wholesaler selling these products to international clients. We already have a name and logo of our company, hence please view attached current card design. We need a completely new design to compliment our business and industry and the final design should be new and elegant.

Contact Information for Business Card

New card details must be same as per current card. Like logo, name, tel no. & etc.

Colors

Designer to choose colors to be used in the design.

```html
<!DOCTYPE html>
<html lang="en">
<head>
<meta charset="utf-8">
<title>Varden Gold — Business Card</title>
<link rel="stylesheet" href="https://fonts.googleapis.com/css2?family=Bebas+Neue&family=Open+Sans:wght@400;600&display=swap">
<style>
  :root {
    --backdrop: #3b3532;
    --card: #121212;
    --gold: #e9a012;
    --silver: #d9d9d9;
    --text-muted: #b9b9b9;
    --divider: #3a3a3a;
  }
  * { margin: 0; padding: 0; box-sizing: border-box; }
  html, body { width: 1200px; height: 844px; overflow: hidden; }
  body {
    background: var(--backdrop);
    font-family: "Open Sans", Arial, sans-serif;
    position: relative;
  }
  .card {
    position: absolute;
    top: 279px;
    width: 500px;
    height: 286px;
    background: var(--card);
    box-shadow: 0 18px 40px rgba(0,0,0,.45);
  }
  .card--front { left: 70px; }
  .card--back { left: 630px; }

  /* Brand wordmark: plain text in the body font */
  .brand {
    position: absolute;
    left: 0; top: 0;
    width: 262px; height: 100%;
    display: flex;
    align-items: center;
    justify-content: center;
  }
  .brand__name {
    font-family: "Open Sans", Arial, sans-serif;
    font-weight: 600;
    font-size: 30px;
    line-height: 1;
    color: var(--gold);
    white-space: nowrap;
  }
  .card__divider {
    position: absolute;
    left: 262px; top: 36px;
    width: 1px; height: 214px;
    background: var(--divider);
  }

  /* Front: contact side */
  .contact {
    position: absolute;
    left: 282px; top: 44px;
    right: 16px;
    color: var(--text-muted);
    font-size: 12.5px;
    line-height: 1.35;
  }
  .contact__name {
    font-family: "Bebas Neue", Impact, sans-serif;
    font-size: 21px;
    line-height: 1;
    color: var(--gold);
    letter-spacing: .5px;
  }
  .contact__role { margin-bottom: 14px; }
  .contact__address { margin-bottom: 12px; }
  .contact__list { list-style: none; }
  .contact__item {
    display: flex;
    align-items: center;
    gap: 8px;
  }
  .contact__icon { width: 11px; height: 11px; fill: var(--gold); flex: none; }

  /* Back */
  .card--back .brand { width: 100%; }
  .card--back .brand__name {
    font-size: 36px;
    color: var(--silver);
  }
</style>
</head>
<body>

<section class="card card--front" aria-label="Business card front">
  <div class="brand">
    <span class="brand__name">Varden Gold</span>
  </div>
  <div class="card__divider"></div>
  <div class="contact">
    <p class="contact__name">Ravin Solanki</p>
    <p class="contact__role">Director</p>
    <p class="contact__address">12 Lantern Quay Rd,<br>Singapore 208810</p>
    <ul class="contact__list">
      <li class="contact__item">
        <svg class="contact__icon" viewBox="0 0 12 12" aria-label="Telephone"><path d="M1 4c0-2 2-3 5-3s5 1 5 3H8.5V3h-5v1zM2 5h8l1 6H1z"/></svg>
        +65 6100 2480
      </li>
      <li class="contact__item">
        <svg class="contact__icon" viewBox="0 0 12 12" aria-label="Mobile"><path d="M3 0h6a1 1 0 0 1 1 1v10a1 1 0 0 1-1 1H3a1 1 0 0 1-1-1V1a1 1 0 0 1 1-1zm0 2v7h6V2z"/></svg>
        +65 9120 4471
      </li>
      <li class="contact__item">
        <svg class="contact__icon" viewBox="0 0 12 12" aria-label="Fax"><path d="M3 0h6v4H3zM1 5h10v5H9v2H3v-2H1zm3 4v2h4V9z"/></svg>
        +65 6100 2481
      </li>
      <li class="contact__item">
        <svg class="contact__icon" viewBox="0 0 12 12" aria-label="Email"><path d="M0 2h12v1L6 7 0 3zm0 2.5l6 4 6-4V10H0z"/></svg>
        ravin@vardengold.com
      </li>
    </ul>
  </div>
</section>

<section class="card card--back" aria-label="Business card back">
  <div class="brand">
    <span class="brand__name">Varden Gold</span>
  </div>
</section>

</body>
</html>
```